New Web Design Project

Number of Pages Required

1 page

Requirements
Must have
• An Overview / Background of the Business & Services(not for profit rescue animal farm)
• The Target Market / Audience you are trying to reach (animal lovers)
• Design Specifics; any preferences or ideas for Style, Colour, Imagery, etc (no preferences)

```html
<!DOCTYPE html>
<html lang="en">
<head>
<meta charset="utf-8">
<title>Maple Hollow Farms</title>
<link href="https://fonts.googleapis.com/css2?family=Nunito+Sans:wght@400;600;700;800&family=Open+Sans:wght@400;600&display=swap" rel="stylesheet">
<style>
:root{
  --green:#3a7a22;
  --green-dark:#2f6a1a;
  --ink:#222222;
  --body:#555555;
  --white:#ffffff;
  --paper:#ececec;
  --footer:#1e1e1e;
  --field-line:#dcdcdc;
}
*{box-sizing:border-box;margin:0;padding:0}
html,body{width:1200px;height:3416px;overflow:hidden}
body{font-family:"Open Sans",Arial,sans-serif;color:var(--body);background:var(--white)}
.page{position:relative;width:1200px;height:3416px}
section,footer{position:absolute;left:0;width:1200px}
.center{position:absolute;left:0;width:100%;text-align:center}
.heading{font-family:"Nunito Sans",Arial,sans-serif;font-weight:800;color:var(--ink);font-size:39px;letter-spacing:.5px}

/* hero */
.hero{top:0;height:742px;overflow:hidden}
.hero-photo{position:absolute;inset:0;background:
  linear-gradient(180deg,rgba(10,30,10,.35) 0%,rgba(0,0,0,.15) 40%,rgba(0,0,0,.2) 100%),
  linear-gradient(180deg,#3c5a2e 0%,#4f7a36 35%,#5f9a3c 60%,#4e8a2e 78%,#2c3e22 100%)}
.brand{position:absolute;left:92px;top:28px;width:320px;text-align:center}
.brand-mark{display:block;width:80px;height:80px;border-radius:50%;background:var(--green);margin:0 auto 6px}
.brand-name{display:block;white-space:nowrap;font-family:"Nunito Sans",Arial,sans-serif;font-weight:800;font-size:24px;line-height:30px;color:var(--white);letter-spacing:.2px}
.nav{position:absolute;top:110px;left:505px;display:flex;gap:0;list-style:none}
.nav li{font-family:"Nunito Sans",Arial,sans-serif;font-weight:600;font-size:18px;color:var(--white);margin-right:42px;position:relative;white-space:nowrap}
.nav li:last-child{margin-right:0}
.nav li.active::after{content:"";position:absolute;left:0;right:0;bottom:-6px;height:2px;background:var(--white)}
.hero-title{top:300px;font-family:"Nunito Sans",Arial,sans-serif;font-weight:800;font-size:62px;color:var(--white);letter-spacing:1px}
.hero-sub{top:383px;font-family:"Nunito Sans",Arial,sans-serif;font-weight:600;font-size:19px;color:var(--white);letter-spacing:.5px}
.btn-outline{position:absolute;left:501px;top:449px;width:198px;height:50px;border:2px solid var(--white);border-radius:25px;color:var(--white);font-family:"Nunito Sans",Arial,sans-serif;font-weight:600;font-size:17px;display:flex;align-items:center;justify-content:center}
.slide-arrow{position:absolute;right:12px;top:366px}

/* welcome */
.welcome{top:742px;height:806px;background:var(--white)}
.welcome .heading{top:78px}
.intro{position:absolute;left:180px;width:840px;top:143px;text-align:center;font-size:15px;line-height:29px}
.card{position:absolute;top:255px;width:313px}
.card-photo{position:relative;height:353px;overflow:hidden}
.card-photo .shade{position:absolute;inset:0;background:linear-gradient(180deg,rgba(0,0,0,0) 40%,rgba(0,0,0,.45) 100%)}
.card-title{position:absolute;left:0;right:0;top:255px;text-align:center;font-family:"Nunito Sans",Arial,sans-serif;font-weight:700;font-size:27px;color:var(--white)}
.card-rule{position:absolute;left:124px;width:66px;top:314px;height:3px;background:var(--white)}
.card-text{margin-top:30px;text-align:center;font-size:14px;line-height:28px;padding:0 8px}
.photo-goats{background:linear-gradient(160deg,#6b6a4a 0%,#4a3f30 45%,#2a2420 100%)}
.photo-cow{background:linear-gradient(170deg,#7b7b70 0%,#4a4640 45%,#2c2a28 100%)}
.photo-sheep{background:linear-gradient(175deg,#5e6458 0%,#4f5446 40%,#a8a69a 75%,#6e6c60 100%)}

/* about */
.about{top:1548px;height:718px;overflow:hidden}
.about-photo{position:absolute;inset:0;background:
  linear-gradient(180deg,#6a7078 0%,#7b7f80 25%,#5a6a4a 38%,#3f6a3c 60%,#2f5a34 100%)}
.about .heading{top:100px;color:var(--white)}
.about-box{position:absolute;left:255px;top:194px;width:690px;height:371px;background:rgba(20,20,20,.72)}
.about-text{position:absolute;left:60px;right:60px;top:52px;text-align:center;color:#e8e8e8;font-size:15px;line-height:28.5px}
.btn-solid{position:absolute;background:var(--green);color:var(--white);border-radius:26px;display:flex;align-items:center;justify-content:center;font-family:"Nunito Sans",Arial,sans-serif;font-weight:700;font-size:17px}
.about .btn-solid{left:237px;top:259px;width:216px;height:51px}

/* contact */
.contact{top:2266px;height:822px;background:var(--paper)}
.contact .heading{top:82px}
.info{position:absolute;top:200px;width:300px;text-align:center}
.info-icon{width:74px;height:74px;border:2px solid var(--green);border-radius:50%;margin:0 auto;display:flex;align-items:center;justify-content:center}
.info-label{margin-top:14px;font-family:"Nunito Sans",Arial,sans-serif;font-weight:800;font-size:20px;color:var(--ink)}
.info-text{margin-top:6px;font-size:15px;line-height:24px;color:#444}
.field{position:absolute;background:var(--white);border:1px solid var(--field-line);border-radius:22px;font-size:15px;color:#777;padding:0 22px;display:flex;align-items:center}
.field.message{align-items:flex-start;padding-top:18px;border-radius:26px}
.contact .btn-solid{left:521px;top:687px;width:158px;height:48px}

/* footer */
.footer{top:3088px;height:328px;background:var(--footer)}
.footer .brand{left:0;width:1200px;top:46px}
.footer .brand-mark{width:72px;height:72px}
.footer .brand-name{font-size:23px}
.footer-links{position:absolute;top:190px;left:0;width:100%;display:flex;justify-content:center;list-style:none}
.footer-links li{font-size:12px;color:#e0e0e0;padding:0 16px;border-left:1px solid #666}
.footer-links li:first-child{border-left:none}
.copyright{top:270px;font-size:12px;color:#d0d0d0}
</style>
</head>
<body>
<div class="page">

  <section class="hero">
    <div class="hero-photo" role="img" aria-label="Sheep grazing on a green meadow beneath tall trees, with a wooden fence in front"></div>
    <div class="brand">
      <span class="brand-mark"></span>
      <span class="brand-name">MAPLE HOLLOW FARMS</span>
    </div>
    <ul class="nav">
      <li class="active">HOME</li>
      <li>ABOUT US</li>
      <li>OUR SERVICES</li>
      <li>BLOG</li>
      <li>CONTACT US</li>
    </ul>
    <h1 class="center hero-title">RESCUE ANIMAL FARM</h1>
    <p class="center hero-sub">ET HARUM QUIDEM RERUM FACILIS EST ET EXPEDITA DISTINCTIO</p>
    <div class="btn-outline">LEARN MORE</div>
    <svg class="slide-arrow" width="14" height="30" viewBox="0 0 14 30"><path d="M2 2 L12 15 L2 28" fill="none" stroke="rgba(255,255,255,.6)" stroke-width="2"/></svg>
  </section>

  <section class="welcome">
    <h2 class="center heading">WELCOME TO MAPLE HOLLOW FARMS</h2>
    <p class="intro">Sed ut perspiciatis unde omnis iste natus error sit voluptatem accusantium doloremque laudantium, totam rem aperiam, eaque ipsa quae ab illo inventore veritatis et quasi architecto beatae vitae dicta sunt explicabo.</p>

    <div class="card" style="left:112px">
      <div class="card-photo photo-goats" role="img" aria-label="Goats standing together in a pen"><div class="shade"></div>
        <div class="card-title">NUMQUAM EIUS</div><div class="card-rule"></div></div>
      <p class="card-text">Lorem ipsum dolor sit amet, consectetur adipiscing elit, sed do eiusmod tempor incididunt ut labore et dolore magna</p>
    </div>
    <div class="card" style="left:444px">
      <div class="card-photo photo-cow" role="img" aria-label="A black cow standing in a muddy yard"><div class="shade"></div>
        <div class="card-title">MINIMA VENIA</div><div class="card-rule"></div></div>
      <p class="card-text">Lorem ipsum dolor sit amet, consectetur adipiscing elit, sed do eiusmod tempor incididunt ut labore et dolore magna</p>
    </div>
    <div class="card" style="left:776px">
      <div class="card-photo photo-sheep" role="img" aria-label="Sheep gathered under a hay feeder shelter"><div class="shade"></div>
        <div class="card-title">REM APERIAM</div><div class="card-rule"></div></div>
      <p class="card-text">Lorem ipsum dolor sit amet, consectetur adipiscing elit, sed do eiusmod tempor incididunt ut labore et dolore magna</p>
    </div>
  </section>

  <section class="about">
    <div class="about-photo" role="img" aria-label="Plowed green field beside a farm barn under a grey sky"></div>
    <h2 class="center heading">ABOUT US</h2>
    <div class="about-box">
      <p class="about-text">At vero eos et accusamus et iusto odio dignissimos ducimus qui blanditiis praesentium voluptatum deleniti atque corrupti quos dolores et quas molestias excepturi sint occaecati cupiditate non provident, similique sunt in culpa qui officia deserunt mollitia animi, id est laborum et dolorum fuga. Et harum quidem rerum facilis est et expedita distinctio. Nam libero tempore, cum soluta nobis est eligendi optio cumque nihil impedit quo minus id quod maxime</p>
      <div class="btn-solid">MORE ABOUT US</div>
    </div>
  </section>

  <section class="contact">
    <h2 class="center heading">CONTACT US</h2>

    <div class="info" style="left:128px">
      <div class="info-icon"><svg width="26" height="32" viewBox="0 0 26 32"><path d="M13 1C6.4 1 1 6.2 1 12.6 1 21 13 31 13 31s12-10 12-18.4C25 6.2 19.6 1 13 1z" fill="var(--green)"/><circle cx="13" cy="12.5" r="4.5" fill="var(--paper)"/></svg></div>
      <div class="info-label">ADDRESS</div>
      <div class="info-text">P.O. Box 12345, Maple Hollow<br>Farms, City Name</div>
    </div>
    <div class="info" style="left:447px">
      <div class="info-icon"><svg width="28" height="28" viewBox="0 0 24 24"><path d="M6.6 10.8a15.1 15.1 0 0 0 6.6 6.6l2.2-2.2a1 1 0 0 1 1-.25 11.4 11.4 0 0 0 3.6.57 1 1 0 0 1 1 1V20a1 1 0 0 1-1 1A17 17 0 0 1 3 4a1 1 0 0 1 1-1h3.5a1 1 0 0 1 1 1c0 1.25.2 2.45.57 3.57a1 1 0 0 1-.25 1z" fill="var(--green)"/></svg></div>
      <div class="info-label">PHONE</div>
      <div class="info-text">+001(23) 456 789</div>
    </div>
    <div class="info" style="left:772px">
      <div class="info-icon"><svg width="28" height="22" viewBox="0 0 28 22"><rect x="1" y="1" width="26" height="20" rx="2" fill="var(--green)"/><path d="M2 3 L14 12 L26 3" fill="none" stroke="var(--paper)" stroke-width="2"/></svg></div>
      <div class="info-label">EMAIL</div>
      <div class="info-text">info@maplehollowfarms.com</div>
    </div>

    <div class="field" style="left:157px;top:430px;width:285px;height:43px">First Name</div>
    <div class="field" style="left:458px;top:430px;width:284px;height:43px">Email Address</div>
    <div class="field" style="left:758px;top:430px;width:283px;height:43px">Phone Number</div>
    <div class="field message" style="left:157px;top:498px;width:884px;height:135px">Message</div>
    <div class="btn-solid">SEND</div>
  </section>

  <footer class="footer">
    <div class="brand">
      <span class="brand-mark"></span>
      <span class="brand-name">MAPLE HOLLOW FARMS</span>
    </div>
    <ul class="footer-links">
      <li>Home</li><li>About Us</li><li>Our Services</li><li>Blog</li><li>Contact Us</li>
    </ul>
    <p class="center copyright">Copyrights © 2019. Maple Hollow Farms. All rights reserved.</p>
  </footer>

</div>
</body>
</html>
```